TA BRAMLEY BUSINESS CARD DESIGN PROJECT

We need to utilize our logo that was expertly created on PixelHarbor and now need to match this with a business card design.

```html
<!DOCTYPE html>
<html lang="en">
<head>
<meta charset="utf-8">
<title>TA BRAMLEY Business Card</title>
<link href="https://fonts.googleapis.com/css2?family=Open+Sans:wght@400;600;700;800&display=swap" rel="stylesheet">
<style>
  :root {
    --backdrop: #333333;
    --card-dark: #1d1d1d;
    --brand-blue: #1558a8;
    --ink-white: #ffffff;
    --divider: #d9d9d9;
  }
  * { margin: 0; padding: 0; box-sizing: border-box; }
  html, body {
    width: 1200px; height: 780px; overflow: hidden;
    background: var(--backdrop);
    font-family: "Open Sans", Arial, sans-serif;
  }
  .canvas {
    width: 1200px; height: 780px;
    display: flex; flex-direction: column; align-items: center; justify-content: center;
    gap: 30px;
  }
  .card {
    position: relative;
    width: 600px; height: 343px;
    overflow: hidden;
  }
  /* Back side */
  .card-back {
    background: var(--brand-blue);
    display: flex; align-items: center; justify-content: center;
  }
  .card-back .brand-name {
    color: var(--ink-white);
    font-weight: 800;
    font-size: 62px;
    letter-spacing: 4px;
  }
  /* Front side */
  .card-front { background: var(--card-dark); }
  .front-brand {
    position: absolute; left: 30px; top: 112px; width: 250px;
    text-align: center;
    color: var(--brand-blue);
    font-weight: 800; font-size: 34px; letter-spacing: 3px; line-height: 1.1;
  }
  .divider {
    position: absolute; left: 300px; top: 40px;
    width: 1px; height: 200px;
    background: var(--divider);
  }
  .contact-block { position: absolute; left: 328px; top: 58px; }
  .person-name {
    color: var(--brand-blue);
    font-weight: 700; font-size: 27px; line-height: 1.1;
  }
  .person-title {
    color: var(--ink-white);
    font-weight: 600; font-size: 15px; margin-top: 4px;
  }
  .contact-list { list-style: none; margin-top: 22px; }
  .contact-list li {
    display: flex; align-items: center; gap: 10px;
    color: var(--ink-white); font-size: 14px; line-height: 24px;
  }
  .contact-list svg { width: 14px; height: 14px; flex: none; }
  .address-band {
    position: absolute; left: 0; top: 272px;
    width: 468px; height: 30px;
    background: var(--brand-blue);
    color: var(--ink-white);
    font-size: 14px; line-height: 30px;
    padding-left: 36px;
  }
  .band-brand {
    position: absolute; left: 480px; top: 272px;
    height: 30px; line-height: 30px;
    color: var(--brand-blue);
    font-weight: 800; font-size: 14px; letter-spacing: 1px;
  }
</style>
</head>
<body>
<main class="canvas">
  <section class="card card-back" aria-label="Business card back">
    <span class="brand-name">TA BRAMLEY</span>
  </section>

  <section class="card card-front" aria-label="Business card front">
    <div class="front-brand">TA BRAMLEY</div>
    <div class="divider"></div>
    <div class="contact-block">
      <h1 class="person-name">Mara Kovalenko</h1>
      <p class="person-title">Managing Director</p>
      <ul class="contact-list">
        <li>
          <svg viewBox="0 0 24 24" aria-hidden="true"><path fill="#1558a8" d="M6.6 10.8a15.2 15.2 0 0 0 6.6 6.6l2.2-2.2c.3-.3.7-.4 1-.2 1.1.4 2.3.6 3.6.6.6 0 1 .4 1 1V20c0 .6-.4 1-1 1A17 17 0 0 1 3 4c0-.6.4-1 1-1h3.5c.6 0 1 .4 1 1 0 1.3.2 2.5.6 3.6.1.3 0 .7-.2 1z"/></svg>
          (555) 214-0387
        </li>
        <li>
          <svg viewBox="0 0 24 24" aria-hidden="true"><rect x="2" y="5" width="20" height="14" rx="2" fill="#1558a8"/><path d="M3 6l9 7 9-7" fill="none" stroke="#1d1d1d" stroke-width="1.8"/></svg>
          hello@tabramley.example
        </li>
        <li>
          <svg viewBox="0 0 24 24" aria-hidden="true"><circle cx="12" cy="12" r="10" fill="#1558a8"/><path d="M2 12h20M12 2c3 3 3 17 0 20M12 2c-3 3-3 17 0 20" fill="none" stroke="#1d1d1d" stroke-width="1.4"/></svg>
          www.tabramley.example
        </li>
      </ul>
    </div>
    <div class="address-band">418 Linden Ave. Suite 120 Riverton, TX 75001</div>
    <div class="band-brand">TA BRAMLEY</div>
  </section>
</main>
</body>
</html>
```